BOLD & MINIMALIST DESIGN NEEDED

We want a very bold but minimalistic business card design that is impactful and utilizes both sides of the business card. Our current logo is included for your use.

We want bold fonts and good use of negative space. We don't want the logo to overpower the design.

Target Market(s)

Professionals who are building new commercial buildings.

Industry/Entity Type

Construction

Contact Information for Business Card

Name, Title, email, office phone, cell phone, website

Font styles to use
Serif
Sans Serif

Requirements
Must have
• Bold design!

```html
<!DOCTYPE html>
<html lang="en">
<head>
<meta charset="utf-8">
<title>Summitline Build Co – Business Card</title>
<link rel="stylesheet" href="https://fonts.googleapis.com/css2?family=Montserrat:wght@400;500;700;800&display=swap">
<style>
  :root {
    --page: #3a3a3c;
    --card-white: #ffffff;
    --card-black: #1c1c1c;
    --green: #7cc242;
    --ink: #161616;
    --white: #ffffff;
  }
  * { box-sizing: border-box; margin: 0; padding: 0; }
  html, body {
    width: 1200px; height: 1200px; overflow: hidden;
    background: var(--page);
    font-family: "Montserrat", Arial, sans-serif;
  }
  .canvas {
    position: relative; width: 1200px; height: 1200px;
    display: flex; flex-direction: column; align-items: center; justify-content: center; gap: 52px;
  }
  .card {
    position: relative; width: 900px; height: 514px;
    border-radius: 34px; overflow: hidden;
  }
  /* Front */
  .card--front { background: var(--card-white); }
  .card__band { position: absolute; inset: 0; width: 100%; height: 100%; }
  .brand {
    position: absolute; top: 100px; left: 0; right: 0;
    display: flex; align-items: center; justify-content: center; gap: 18px;
  }
  .brand__mark { width: 34px; height: 34px; background: var(--green); }
  .brand__name {
    font-weight: 800; font-size: 54px; letter-spacing: 1px; color: var(--ink);
  }
  .card--back .brand { top: 228px; }
  .card--back .brand__name { color: var(--white); font-size: 60px; }
  .card--back .brand__mark { width: 40px; height: 40px; }

  .person { position: absolute; left: 88px; top: 238px; }
  .person__name { font-weight: 500; font-size: 40px; color: var(--green); letter-spacing: 0.5px; line-height: 1; }
  .person__title { font-weight: 400; font-size: 30px; color: var(--ink); margin-top: 6px; line-height: 1; }

  .rule {
    position: absolute; left: 88px; right: 48px; top: 322px;
    height: 2px; background: var(--green);
  }
  .contact { position: absolute; display: flex; flex-direction: column; gap: 10px; }
  .contact--phones { left: 88px; top: 338px; }
  .contact__row { display: flex; align-items: center; gap: 14px; font-size: 27px; color: var(--ink); line-height: 1.1; white-space: nowrap; }
  .contact__row svg { width: 28px; height: 30px; flex: none; }
  .contact--email { right: 48px; top: 338px; }
  .contact--web { right: 48px; top: 428px; }
  .contact--web .contact__row { color: var(--white); }

  /* Back */
  .card--back { background: var(--card-black); box-shadow: inset 0 0 0 3px var(--green); }
</style>
</head>
<body>
<main class="canvas">
  <section class="card card--front" aria-label="Business card front">
    <svg class="card__band" viewBox="0 0 900 514" preserveAspectRatio="none" aria-hidden="true">
      <path d="M0 452 L420 452 C470 452 475 392 525 392 L900 392 L900 514 L0 514 Z" fill="var(--green)"/>
      <path d="M0 466 L420 466 C472 466 480 404 532 404 L900 404 L900 514 L0 514 Z" fill="var(--card-black)"/>
    </svg>

    <div class="brand">
      <span class="brand__mark"></span>
      <span class="brand__name">SUMMITLINE BUILD CO</span>
    </div>

    <div class="person">
      <p class="person__name">FULL NAME</p>
      <p class="person__title">TITLE</p>
    </div>

    <div class="rule"></div>

    <div class="contact contact--phones">
      <p class="contact__row">
        <svg viewBox="0 0 24 30" aria-hidden="true"><rect x="5" y="2" width="14" height="26" rx="2.5" fill="none" stroke="var(--green)" stroke-width="2"/><line x1="10" y1="24" x2="14" y2="24" stroke="var(--green)" stroke-width="2"/></svg>
        (000) 000 0000
      </p>
      <p class="contact__row">
        <svg viewBox="0 0 24 24" aria-hidden="true"><path d="M6.6 10.8a15 15 0 0 0 6.6 6.6l2.2-2.2a1 1 0 0 1 1-.25 11.4 11.4 0 0 0 3.6.6 1 1 0 0 1 1 1V20a1 1 0 0 1-1 1A17 17 0 0 1 3 4a1 1 0 0 1 1-1h3.5a1 1 0 0 1 1 1c0 1.25.2 2.45.6 3.6a1 1 0 0 1-.25 1z" fill="var(--green)"/></svg>
        (000) 000 0000
      </p>
    </div>

    <div class="contact contact--email">
      <p class="contact__row">
        <svg viewBox="0 0 30 22" aria-hidden="true"><rect x="1" y="2" width="28" height="18" fill="var(--green)"/><path d="M1 2 L15 13 L29 2" fill="none" stroke="var(--white)" stroke-width="2"/></svg>
        email@company.com
      </p>
    </div>

    <div class="contact contact--web">
      <p class="contact__row">
        <svg viewBox="0 0 24 24" aria-hidden="true"><circle cx="12" cy="12" r="10" fill="none" stroke="var(--green)" stroke-width="2"/><ellipse cx="12" cy="12" rx="4.5" ry="10" fill="none" stroke="var(--green)" stroke-width="1.6"/><line x1="2" y1="12" x2="22" y2="12" stroke="var(--green)" stroke-width="1.6"/></svg>
        www.company.com
      </p>
    </div>
  </section>

  <section class="card card--back" aria-label="Business card back">
    <div class="brand">
      <span class="brand__mark"></span>
      <span class="brand__name">SUMMITLINE BUILD CO</span>
    </div>
  </section>
</main>
</body>
</html>
```